Advertising company unique advertising platform

we need a logo design for a new company based in Australia Melbourne. We develop innovated advertising platform where consumer can use this platform to get regular discount, as business owner they can use this platform for free advertisement. Payment for this advertisement platform only payable every two weeks, when I generate revenue for their business

Industry/Entity Type

Advertising

Contact Information for Business Card

Dale Morven | Co-Founder |Managing Director
Suite 718 240 Wattlebrook Lane Melbourne Vic 3000

ABN 38 614 207 923
Tel: +61 0487 259 318 | Email: dale.morven@plivorantu.com

Font styles to use
Decorative
Script

Requirements
Must have
• Try few different design and some round corner business card
Should not have
• One round corner business card...try 4 different colour background not only black, make sure two side is designed. Be creative so imagine you are giving this to a client make sure has wow factor, if you can also try one design with engrave like all the logo, words look 3d feel
• The word Advertising Platform use attached file font

```html
<!DOCTYPE html>
<html lang="en">
<head>
<meta charset="utf-8">
<title>Brightway Hub – Business Card</title>
<link href="https://fonts.googleapis.com/css2?family=Roboto:wght@400;500;700&display=swap" rel="stylesheet">
<style>
  :root {
    --stage: #3a3a3c;
    --card-back: #141414;
    --card-front: #232323;
    --text-light: #f2f2f2;
    --accent-red: #e8452c;
    --accent-green: #1fd8a0;
    --accent-teal: #19e8a8;
    --accent-blue: #4fb4e6;
    --card-w: 540px;
    --card-h: 310px;
  }
  * { box-sizing: border-box; margin: 0; padding: 0; }
  html, body { width: 1200px; height: 886px; overflow: hidden; }
  body {
    background: var(--stage);
    font-family: "Roboto", Arial, sans-serif;
    display: flex;
    align-items: center;
    justify-content: center;
    gap: 40px;
  }
  .card {
    position: relative;
    width: var(--card-w);
    height: var(--card-h);
    border-radius: 4px;
    overflow: hidden;
    box-shadow: 0 14px 30px rgba(0,0,0,.45);
  }

  /* Back side */
  .card--back {
    background: var(--card-back);
    display: flex;
    flex-direction: column;
    align-items: center;
    justify-content: center;
    gap: 34px;
  }
  .brand {
    display: flex;
    align-items: center;
    gap: 14px;
  }
  .brand__dot {
    width: 46px; height: 46px;
    border-radius: 50%;
    background: var(--text-light);
    flex: none;
  }
  .brand__name {
    font-weight: 700;
    font-size: 38px;
    color: var(--text-light);
    letter-spacing: 1px;
    white-space: nowrap;
  }
  .website {
    color: var(--text-light);
    font-size: 13px;
    letter-spacing: 6px;
  }

  /* Front side */
  .card--front { background: var(--card-front); }
  .card--front .brand {
    position: absolute;
    left: 34px; top: 34px;
    gap: 10px;
  }
  .card--front .brand__dot {
    width: 34px; height: 34px;
    background: var(--accent-red);
  }
  .card--front .brand__name {
    font-size: 28px;
    color: var(--accent-red);
  }
  .contact {
    position: absolute;
    left: 34px; top: 128px;
    color: var(--text-light);
    font-size: 13.5px;
    line-height: 1.45;
    list-style: none;
  }
  .contact__gap { margin-top: 8px; }
  .contact__row { display: flex; align-items: center; gap: 7px; }
  .contact__icon { width: 12px; height: 12px; fill: var(--accent-red); flex: none; }

  .ornament {
    position: absolute;
    left: 305px; top: 20px;
    width: 62px; height: 270px;
    border-radius: 31px;
    background: linear-gradient(180deg, var(--accent-teal) 0%, #2ee0b0 55%, var(--accent-blue) 100%);
  }

  .person {
    position: absolute;
    right: 26px; top: 48px;
    text-align: right;
    text-transform: uppercase;
    white-space: nowrap;
  }
  .person__name {
    color: var(--accent-red);
    font-weight: 500;
    font-size: 19px;
  }
  .person__role {
    color: var(--accent-green);
    font-weight: 500;
    font-size: 13.5px;
    line-height: 1.2;
  }
</style>
</head>
<body>

  <section class="card card--back" aria-label="Card back">
    <div class="brand">
      <span class="brand__dot"></span>
      <span class="brand__name">Brightway Hub</span>
    </div>
    <p class="website">www.plivorantu.com</p>
  </section>

  <section class="card card--front" aria-label="Card front">
    <div class="brand">
      <span class="brand__dot"></span>
      <span class="brand__name">Brightway Hub</span>
    </div>

    <ul class="contact">
      <li>Plivorantu</li>
      <li>ABN 38 614 207 923</li>
      <li class="contact__gap">Suite 718 240 Wattlebrook Lane</li>
      <li>Melbourne Vic 3000</li>
      <li class="contact__row contact__gap">
        <svg class="contact__icon" viewBox="0 0 24 24" aria-hidden="true"><path d="M6.6 10.8a15 15 0 0 0 6.6 6.6l2.2-2.2c.3-.3.7-.4 1-.2 1.1.4 2.3.6 3.6.6.6 0 1 .4 1 1V20c0 .6-.4 1-1 1A17 17 0 0 1 3 4c0-.6.4-1 1-1h3.5c.6 0 1 .4 1 1 0 1.3.2 2.5.6 3.6.1.3 0 .7-.2 1z"/></svg>
        +61 0487 259 318
      </li>
      <li class="contact__row">
        <svg class="contact__icon" viewBox="0 0 24 24" aria-hidden="true"><path d="M2 5h20v14H2zM4 7v.4l8 5 8-5V7z"/></svg>
        dale.morven@plivorantu.com
      </li>
    </ul>

    <div class="ornament" role="img" aria-label="Decorative teal-to-blue flowing ribbon ornament"></div>

    <div class="person">
      <p class="person__name">Dale Morven</p>
      <p class="person__role">Co-Founder</p>
      <p class="person__role">Managing Director</p>
    </div>
  </section>

</body>
</html>
```